Corporate Travel Technology Company needs new Business Card design

We need a new business card design to reflect our re-branded company. Our company is called tolvEn (pronounced tolvenn) and we provide Business Intelligence and mobile travel management solutions for the corporate travel industry. Our multinational customers use our solutions to manage large travel budgets and frequent travellers, as well as to save money and reduce risk. We'd like to see designs that use the blue and green palette as well as our corporate logo (attached below). The design should communicate innovation, insight, forward thinking, contemporary, trusted.

Target Market(s)

Large multinational corporates and Travel Agencies.

Industry/Entity Type

Business

Contact Information for Business Card

Rosalind Mercer
Chief Executive
tolvEn
Phone number - +61 (0)2 8134 2907
Email address - rosalind.mercer@tolven-example.com
Mobile number - +61 (0)438 516 702
www.tolven-example.com

Font styles to use
Other font styles liked:
• Please use font as close to corporate logo as possible

Colors
0255a3
0393ce
00a990
33b8a4
33a6d7
3176b5

Requirements
Must have
• Please include the words;
• Mobile Travel Management
• Accelerating Travel Business Insights
• Use corporate logo - although icon can be stylised if needed

```html
<!DOCTYPE html>
<html lang="en">
<head>
<meta charset="utf-8">
<title>tolvEn business card</title>
<link rel="stylesheet" href="https://fonts.googleapis.com/css2?family=Open+Sans:wght@400;600;700&display=swap">
<style>
  :root {
    --backdrop: #e4e6e6;
    --card-white: #ffffff;
    --slate: #3f4d4d;
    --teal-panel: #475e5b;
    --brand-blue: #1ea3dc;
    --text-dark: #2f3a3a;
    --text-grey: #4b5757;
    --shadow: rgba(0, 0, 0, 0.18);
  }
  * { box-sizing: border-box; margin: 0; padding: 0; }
  html, body {
    width: 1200px; height: 844px; overflow: hidden;
    background: var(--backdrop);
    font-family: "Open Sans", Arial, sans-serif;
  }
  .stage {
    position: relative; width: 1200px; height: 844px;
    display: flex; align-items: center; justify-content: center; gap: 50px;
  }
  .card {
    position: relative; width: 525px; height: 300px;
    background: var(--card-white);
    box-shadow: 0 6px 18px var(--shadow);
    overflow: hidden;
  }

  /* Brand wordmark: plain uppercase name with one circle before it */
  .wordmark {
    display: flex; align-items: center; gap: 12px;
    font-weight: 600; line-height: 1;
    text-transform: uppercase; letter-spacing: 6px;
  }
  .wordmark-dot { border-radius: 50%; flex: none; }

  /* Front */
  .card-front .wordmark {
    position: absolute; top: 56px; right: 36px;
    font-size: 34px; color: var(--brand-blue);
  }
  .card-front .wordmark-dot { width: 14px; height: 14px; background: var(--brand-blue); }
  .contact-block { position: absolute; left: 40px; bottom: 30px; }
  .person-name { font-size: 19px; font-weight: 700; color: var(--brand-blue); line-height: 24px; }
  .person-title { font-size: 13px; color: var(--text-dark); margin-bottom: 14px; }
  .contact-list { list-style: none; }
  .contact-list li {
    display: flex; align-items: center; gap: 10px;
    font-size: 14px; color: var(--text-dark); line-height: 22px;
  }
  .contact-list svg { width: 12px; height: 12px; fill: var(--brand-blue); flex: none; }

  /* Back */
  .brand-panel {
    position: absolute; top: 0; left: 0; right: 0; height: 172px;
    background: var(--teal-panel);
  }
  .card-back .wordmark {
    position: absolute; top: 104px; right: 36px;
    font-size: 34px; color: var(--card-white);
  }
  .card-back .wordmark-dot { width: 14px; height: 14px; background: var(--card-white); }
  .tagline-list {
    position: absolute; top: 196px; right: 36px; list-style: none; text-align: right;
  }
  .tagline-list li {
    display: flex; align-items: center; justify-content: flex-end; gap: 8px;
    font-size: 12.5px; text-transform: uppercase; letter-spacing: 0.3px;
    color: var(--text-grey); line-height: 22px;
  }
  .tagline-list svg { width: 11px; height: 11px; stroke: var(--brand-blue); fill: none; stroke-width: 2; }
</style>
</head>
<body>
<main class="stage">
  <section class="card card-front" aria-label="Business card front">
    <div class="wordmark"><span class="wordmark-dot"></span><span>tolvEn</span></div>
    <div class="contact-block">
      <p class="person-name">Rosalind Mercer</p>
      <p class="person-title">Chief Executive</p>
      <ul class="contact-list">
        <li><svg viewBox="0 0 24 24" aria-hidden="true"><path d="M6.6 10.8a15 15 0 0 0 6.6 6.6l2.2-2.2a1 1 0 0 1 1-.25 11.4 11.4 0 0 0 3.6.57 1 1 0 0 1 1 1V20a1 1 0 0 1-1 1A17 17 0 0 1 3 4a1 1 0 0 1 1-1h3.5a1 1 0 0 1 1 1c0 1.25.2 2.45.57 3.57a1 1 0 0 1-.25 1z"/></svg>+61 (0)2 8134 2907</li>
        <li><svg viewBox="0 0 24 24" aria-hidden="true"><path d="M7 1h10a2 2 0 0 1 2 2v18a2 2 0 0 1-2 2H7a2 2 0 0 1-2-2V3a2 2 0 0 1 2-2zm0 3v13h10V4zm5 15a1 1 0 1 0 0 2 1 1 0 0 0 0-2z"/></svg>+61 (0)438 516 702</li>
        <li><svg viewBox="0 0 24 24" aria-hidden="true"><path d="M2 5h20v14H2zm2 2v.5l8 5 8-5V7l-8 5z"/></svg>rosalind.mercer@tolven-example.com</li>
        <li><svg viewBox="0 0 24 24" aria-hidden="true"><path d="M10.6 13.4a1 1 0 0 1 0-1.4l3.5-3.5a1 1 0 1 1 1.4 1.4L12 13.4a1 1 0 0 1-1.4 0zM8 12l-3 3a3 3 0 0 0 4.2 4.2l3-3 1.4 1.4-3 3A5 5 0 0 1 3.6 13.6l3-3zm8 0 3-3a3 3 0 0 0-4.2-4.2l-3 3-1.4-1.4 3-3a5 5 0 0 1 7 7l-3 3z"/></svg>www.tolven-example.com</li>
      </ul>
    </div>
  </section>

  <section class="card card-back" aria-label="Business card back">
    <div class="brand-panel"></div>
    <div class="wordmark"><span class="wordmark-dot"></span><span>tolvEn</span></div>
    <ul class="tagline-list">
      <li><svg viewBox="0 0 12 12" aria-hidden="true"><path d="M2 6.5l2.5 2.5L10 3"/></svg>Mobile Travel Management</li>
      <li><svg viewBox="0 0 12 12" aria-hidden="true"><path d="M2 6.5l2.5 2.5L10 3"/></svg>Accelerating Travel Business Insights</li>
    </ul>
  </section>
</main>
</body>
</html>
```